International business needs business cards

Our company, DRV Ventures Inc. is in the business of supplying a range construction products with particular emphasis on CEMENT. We have developed our own brand - TORVAN SUPPLIES - with which to infiltrate the market. We are launching our brand of cement (TORVAN Type IS Cement) into the Caribbean which is unlike anything this market has ever seen. A monopoly has existed here for the past 60-odd years and the market has now opened to allow the importation of other brands and consumers are anxious and ready for change/improvement. We are very excited to be launching and want to make a great first impression. We will be conducting workshops and seminars (from government level to the hardware store owners) and we want our business card to give us the strong, confident introduction that we need.

Target Market(s)

construction; builders; engineers; home owners

Industry/Entity Type

Construction

Contact Information for Business Card

Marisol Depree
CEO
cell # 1 555 4180736
Ground floor,Lindell Plaza Suite 2734
George Town,Grand Cayman
Cayman Islands,KY1-4823
EMAIL: m.depree@drvventuresinc.example
web site drvventuresinc.example

COMPANY: skype info drv.ventures.example

second card
Yvette Brannock-Depree
CFO
CELL# 1 555 607 3941
George Town,Grand Cayman
Cayman Islands,KY1-4823
EMAIL: y.brannockdepree@drvventuresinc.example
website drvventuresinc.example

Requirements
Must have
• Business cards must display BOTH logos - DRV is the company and TORVAN is the brand.

```html
<!DOCTYPE html>
<html lang="en">
<head>
<meta charset="utf-8">
<title>DRV Ventures Inc. – Business Card</title>
<link rel="stylesheet" href="https://fonts.googleapis.com/css2?family=Open+Sans:wght@400;600&display=swap">
<style>
  :root {
    --page: #e9e6e1;
    --card-white: #ffffff;
    --brand-red: #7e1418;
    --name-red: #8a1c22;
    --ink: #1a1a1a;
    --grey: #6b6b6b;
    --light-grey: #9a9a9a;
    --white: #ffffff;
  }
  * { box-sizing: border-box; margin: 0; padding: 0; }
  html, body { width: 1200px; height: 950px; overflow: hidden; }
  body {
    background: var(--page);
    font-family: "Open Sans", Arial, sans-serif;
    position: relative;
  }
  .card {
    position: absolute;
    width: 700px;
    height: 400px;
    border-radius: 4px;
    box-shadow: 0 6px 18px rgba(0,0,0,0.18);
    overflow: hidden;
  }
  .card--front { left: 60px; top: 60px; background: var(--card-white); }
  .card--back { left: 440px; top: 500px; background: var(--brand-red); }

  /* company wordmark: one font, one weight, one colour */
  .company { position: absolute; display: flex; align-items: center; gap: 16px; }
  .company__square { width: 64px; height: 64px; background: var(--brand-red); flex: none; }
  .company__name {
    font-family: "Open Sans", Arial, sans-serif;
    font-weight: 600;
    font-size: 28px;
    line-height: 1;
    color: var(--ink);
    white-space: nowrap;
  }
  .card--front .company { left: 48px; top: 64px; }

  .person { position: absolute; left: 48px; top: 196px; }
  .person__name { font-size: 26px; color: var(--name-red); font-weight: 400; line-height: 1.1; }
  .person__title { font-size: 15px; color: var(--grey); margin-top: 2px; }

  .address { position: absolute; left: 48px; top: 268px; font-size: 15px; line-height: 1.45; color: var(--grey); font-style: normal; }

  .brand { position: absolute; right: 52px; top: 48px; display: flex; align-items: center; gap: 10px; color: var(--grey); font-weight: 600; font-size: 18px; letter-spacing: 2px; }
  .brand__circle { width: 34px; height: 34px; border-radius: 50%; background: var(--light-grey); }

  .contact { position: absolute; right: 52px; top: 150px; font-size: 15px; line-height: 1.55; color: var(--grey); }
  .contact__label { color: var(--name-red); font-weight: 600; }

  .edge-band { position: absolute; left: 0; bottom: 0; width: 100%; height: 10px; background: var(--brand-red); }

  /* back */
  .card--back .company { left: 60px; top: 90px; }
  .card--back .company__name { font-size: 40px; }
  .back__web { position: absolute; left: 60px; top: 160px; color: var(--white); font-size: 17px; letter-spacing: 0.5px; }
</style>
</head>
<body>
  <section class="card card--front" aria-label="Business card front">
    <div class="company">
      <div class="company__square"></div>
      <p class="company__name">DRV Ventures Inc.</p>
    </div>

    <div class="brand">
      <span class="brand__circle"></span>
      <span>TORVAN SUPPLIES</span>
    </div>

    <div class="person">
      <p class="person__name">Marisol Depree</p>
      <p class="person__title">CEO</p>
    </div>

    <address class="address">
      Ground floor<br>
      Lindell Plaza Suite 2734<br>
      George Town,Grand Cayman<br>
      Cayman Islands,KY1-4823
    </address>

    <div class="contact">
      <p><span class="contact__label">Mobile:</span> 1 555 4180736</p>
      <p>m.depree@drvventuresinc.example</p>
      <p>www.drvventuresinc.example</p>
    </div>

    <div class="edge-band"></div>
  </section>

  <section class="card card--back" aria-label="Business card back">
    <div class="company">
      <p class="company__name">DRV Ventures Inc.</p>
    </div>
    <p class="back__web">www.drvventuresinc.example</p>
  </section>
</body>
</html>
```